Kentucky residential recovery center needs a flyer design

We need a flyer design for a 16 bed male residential/inpatient recovery center based in Richmond, Kentucky. The facility provides short term (average 30 day) treatment to those struggling with substace abuse and addiction. The design should communicate trust, assurance, safety.
Our wesite provides more information https://corvalmend.org/treatment-services/residential-treatment/

Target Market(s)

Men (typically 30-50) struggling with substance addiction

```html
<!DOCTYPE html>
<html lang="en">
<head>
<meta charset="utf-8">
<title>Corvalmend Residential Recovery Flyer</title>
<link href="https://fonts.googleapis.com/css2?family=Poppins:wght@400;500;600;700;800&family=Oswald:wght@500;600&display=swap" rel="stylesheet">
<style>
:root{
  --navy:#0d1180;
  --sky:#4a9be8;
  --sky-light:#8cc3f2;
  --quote-bg:#d3e8fb;
  --green:#16a32a;
  --lime:#3ad63a;
  --ink:#1a1a2a;
  --stat-bg:#e9ecea;
  --stage:#ffffff;
  --white:#ffffff;
}
*{box-sizing:border-box;margin:0;padding:0}
html,body{width:910px;height:1200px;overflow:hidden;background:var(--stage)}
body{font-family:"Poppins",sans-serif;color:var(--ink)}
.stage{position:relative;width:910px;height:1200px;overflow:hidden}
.page{position:absolute;top:319px;width:670px;height:870px;background:var(--white);overflow:hidden;transform:scale(.645);transform-origin:0 0;box-shadow:0 4px 22px rgba(0,0,0,.16)}
.page-front{left:15px}
.page-back{left:463px}
.abs{position:absolute}
.footer-bar{position:absolute;left:0;bottom:0;width:670px;height:12px;background:var(--green);border-radius:6px 6px 0 0}

/* front */
.hero-ring{left:0;top:0;width:670px;height:380px}
.hl{position:absolute;left:37px;font-weight:800;line-height:1;letter-spacing:-.4px;white-space:nowrap}
.hl-res{top:34px;font-size:40px;color:var(--sky)}
.hl-inp{top:70px;font-size:62px;color:var(--sky)}
.hl-rec{top:124px;font-size:54px;color:var(--navy)}
.hl-cen{top:175px;font-size:54px;color:var(--navy)}
.location-bar{left:42px;top:238px;width:330px;height:24px;background:var(--green);color:var(--white);font-weight:600;font-size:13px;letter-spacing:3.4px;line-height:24px;padding-left:16px;white-space:nowrap}
.tagline{left:41px;top:268px;width:320px;font-size:18px;line-height:1.17}
.badge{left:366px;top:226px;width:128px;height:128px}
.badge-text{left:366px;top:256px;width:128px;text-align:center;color:var(--white)}
.badge-text .title{font-family:"Oswald",sans-serif;font-weight:500;font-size:20px;color:var(--navy);line-height:1}
.badge-text .sub{font-size:10.5px;line-height:1.1;margin-top:2px}
.badge-text .body{font-size:8.3px;line-height:1.15;margin-top:1px}
.issues{left:40px;top:344px;width:592px;height:128px;background:var(--navy);border-radius:10px}
.issues h2{position:absolute;left:27px;top:8px;font-size:17px;font-weight:700;color:var(--lime)}
.issue-list{position:absolute;left:0;top:40px;width:100%;display:flex}
.issue{flex:1;text-align:center;color:var(--white);font-weight:600;font-size:12.5px;line-height:1.15;border-right:1px dashed rgba(140,195,242,.55);height:76px}
.issue:last-child{border-right:none}
.issue svg{display:block;margin:0 auto 6px;height:30px}
.why{left:52px;top:500px;font-size:27px;font-weight:800;color:var(--navy);letter-spacing:-.3px;white-space:nowrap}
.stat{position:absolute;width:116px;height:116px;border-radius:50%;background:radial-gradient(circle at 50% 40%,#f4f5f4 0%,var(--stat-bg) 70%,#d7dbd8 100%);box-shadow:0 7px 8px -5px rgba(0,0,0,.2);text-align:center;padding-top:15px}
.stat .num{font-size:24px;font-weight:800;color:var(--sky);line-height:1}
.stat .label{font-size:10.5px;font-weight:700;color:var(--navy);line-height:1.05}
.stat .note{font-size:8.3px;line-height:1.15;margin:4px auto 0;width:90px;color:#333}
.stat-years{left:48px;top:549px}
.stat-rating{left:180px;top:549px}
.stat-best{left:48px;top:689px;padding-top:8px}
.stat-treated{left:184px;top:689px}
.stat-best .num{font-size:22px}
.stat-best .label{font-size:9.5px}
.rooms{left:328px;top:489px;width:304px;height:200px;display:grid;grid-template-columns:repeat(3,1fr);grid-template-rows:1fr 1fr;gap:2px;background:var(--white)}
.room-a{background:linear-gradient(160deg,#c9b79c,#7d6a54)}
.room-b{background:linear-gradient(160deg,#e0ddd6,#3a3a3c)}
.room-c{background:linear-gradient(160deg,#d8cdbd,#5b4b3d)}
.room-d{background:linear-gradient(160deg,#b5a48f,#6d5a48)}
.room-e{background:linear-gradient(160deg,#a8b6c4,#6b4a36)}
.room-f{background:linear-gradient(160deg,#cfc2b0,#4a3a30)}
.spaces{left:358px;top:559px;width:246px;height:48px;background:var(--green);border:2px solid var(--lime);text-align:center;color:var(--white)}
.spaces h3{font-size:19px;font-weight:700;letter-spacing:2px;color:var(--navy);line-height:1.1;margin-top:2px}
.spaces p{font-size:7.8px;line-height:1.15}
.brand-mark{left:347px;top:722px;width:48px;height:48px;border-radius:50%;background:var(--navy)}
.brand-name{left:316px;top:776px;width:110px;text-align:center;font-size:14px;font-weight:700;color:var(--navy)}
.contact{left:438px;top:712px;width:228px}
.contact .kicker{font-size:9.5px;font-weight:600;color:var(--sky);line-height:1.1;text-transform:uppercase}
.contact .lead{font-size:13.5px;font-weight:600;line-height:1.2;margin-top:3px}
.row{display:flex;align-items:center;gap:6px;font-size:10.5px;margin-top:5px;white-space:nowrap}
.row svg{width:11px;height:11px;flex:none}
.contact .web{font-size:17.5px;font-weight:700;color:var(--navy);margin-top:3px}

/* back */
.back-header{left:0;top:0;width:670px;height:258px;background:var(--navy);border-radius:0 0 36px 36px;overflow:hidden}
.programs-title{left:40px;top:30px;font-size:32px;font-weight:700;line-height:1.02;color:var(--white)}
.programs-title .accent{color:var(--lime);display:block}
.programs-copy{left:40px;top:118px;width:330px;color:var(--white);font-size:9.6px;line-height:1.25}
.programs-copy p+p{margin-top:10px}
.team-photo{left:365px;top:22px;width:275px;height:236px;background:linear-gradient(170deg,#1a2aa0 0%,#b76a78 55%,#8a8f9c 100%)}
.works-title{left:0;top:268px;width:670px;text-align:center;font-size:24px;font-weight:700;letter-spacing:4.6px;color:var(--green)}
.feature{position:absolute;width:275px;display:flex;gap:8px}
.feature .icon{width:44px;height:44px;flex:none;border-radius:50%;border:3px solid var(--green);background:var(--white);display:flex;align-items:center;justify-content:center}
.feature .icon span{width:32px;height:32px;border-radius:50%;background:var(--green);display:block}
.feature h4{font-size:11.5px;font-weight:700;color:var(--sky);line-height:1.1;text-transform:uppercase}
.feature p{font-size:9.5px;line-height:1.2;margin-top:1px}
.f-evidence{left:40px;top:315px}
.f-tele{left:343px;top:315px}
.f-individual{left:40px;top:406px}
.f-mat{left:343px;top:405px}
.quote{position:absolute;top:505px;width:278px;height:142px;background:var(--quote-bg);border-radius:14px;padding:26px 18px 0 18px;font-size:9.8px;line-height:1.25}
.quote .author{font-weight:700;margin-top:8px}
.quote .mark{position:absolute;font-size:44px;font-weight:700;color:var(--sky);line-height:1}
.quote .open{left:14px;top:-12px}
.quote .close{right:14px;bottom:-26px}
.q-left{left:42px}
.q-right{left:361px}
.insure-title{left:0;top:664px;width:670px;text-align:center;font-size:16px;font-weight:700;letter-spacing:3.6px}
.insurers{left:38px;top:696px;width:604px;display:flex;justify-content:space-between;font-size:11px;font-weight:600;color:var(--navy)}
.transport{left:40px;top:740px;width:592px;height:48px;border:2px solid var(--sky);border-radius:24px}
.transport-tag{position:absolute;left:-2px;top:-2px;width:187px;height:48px;background:var(--sky);border-radius:24px;color:var(--white);font-family:"Oswald",sans-serif;font-weight:500;font-size:17px;line-height:1;padding:5px 0 0 20px}
.location{position:absolute;top:6px;display:flex;gap:4px;font-size:8.6px;line-height:1.2}
.location svg{width:9px;height:12px;flex:none;margin-top:1px}
.location b{font-weight:700;font-size:9.4px}
.loc-a{left:192px}
.loc-b{left:400px}
.back-lead{left:40px;top:800px;font-size:13.5px;font-weight:600;line-height:1.2}
.back-rows{left:233px;top:798px}
.back-rows .row{margin-top:3px}
.web-pill{left:425px;top:802px;width:208px;height:30px;border-radius:15px;background:var(--navy);color:var(--white);font-size:16px;font-weight:700;text-align:center;line-height:30px}
</style>
</head>
<body>
<div class="stage">

  <main class="page page-front">
    <svg class="abs hero-ring" viewBox="0 0 670 380">
      <defs>
        <radialGradient id="handsTone" cx="45%" cy="55%" r="60%">
          <stop offset="0%" stop-color="#9a9a9a"/>
          <stop offset="100%" stop-color="#1e1e1e"/>
        </radialGradient>
      </defs>
      <circle cx="522" cy="152" r="150" fill="none" stroke="var(--sky-light)" stroke-width="8"/>
      <circle cx="522" cy="152" r="139" fill="none" stroke="var(--sky)" stroke-width="16"/>
      <circle cx="522" cy="152" r="129" fill="url(#handsTone)" role="img" aria-label="Black and white photo of many hands stacked together in unity"/>
    </svg>

    <h1>
      <span class="hl hl-res">RESIDENTIAL &amp;</span>
      <span class="hl hl-inp">INPATIENT</span>
      <span class="hl hl-rec">RECOVERY</span>
      <span class="hl hl-cen">CENTER</span>
    </h1>

    <div class="abs location-bar">BASED IN RICHMOND, KENTUCKY</div>
    <p class="abs tagline">We offer the most effective and comfortable treatment that leads to success.</p>

    <svg class="abs badge" viewBox="0 0 128 128" aria-hidden="true">
      <circle cx="64" cy="64" r="56" fill="var(--sky)"/>
      <circle cx="64" cy="64" r="58" fill="none" stroke="var(--sky)" stroke-width="10" stroke-dasharray="0 12.6" stroke-linecap="round"/>
      <circle cx="64" cy="64" r="50" fill="none" stroke="var(--white)" stroke-width="1" stroke-dasharray="2.5 2.5"/>
    </svg>
    <div class="abs badge-text">
      <div class="title">SHORT TERM</div>
      <div class="sub">(AVERAGE 30 DAY)</div>
      <div class="body">treatment to those<br>struggling with<br>substace abuse and<br>addiction</div>
    </div>

    <section class="abs issues">
      <h2>WHAT ISSUES CAN BE TREATED?</h2>
      <div class="issue-list">
        <div class="issue">
          <svg viewBox="0 0 40 44"><rect x="6" y="14" width="10" height="28" rx="3" fill="#fff"/><rect x="9" y="4" width="4" height="11" fill="#fff"/><path d="M22 14h14l-2 12a5 5 0 0 1-10 0z" fill="none" stroke="#fff" stroke-width="2.5"/><line x1="29" y1="31" x2="29" y2="41" stroke="#fff" stroke-width="2.5"/><line x1="24" y1="41" x2="34" y2="41" stroke="#fff" stroke-width="2.5"/><rect x="8" y="24" width="6" height="8" fill="var(--green)"/></svg>
          ALCOHOLISM
        </div>
        <div class="issue">
          <svg viewBox="0 0 44 44"><rect x="26" y="12" width="8" height="26" rx="2" fill="none" stroke="#fff" stroke-width="2.5"/><line x1="30" y1="2" x2="30" y2="12" stroke="#fff" stroke-width="2.5"/><line x1="30" y1="38" x2="30" y2="44" stroke="#fff" stroke-width="2"/><path d="M10 6c2 6 2 12 0 18c-2-6-2-12 0-18z M4 14c4 2 6 6 6 10c-4-2-6-6-6-10z M16 14c-4 2-6 6-6 10c4-2 6-6 6-10z" fill="var(--lime)"/><rect x="2" y="30" width="18" height="8" rx="4" fill="#fff"/></svg>
          DRUG<br>ADDICTION
        </div>
        <div class="issue">
          <svg viewBox="0 0 44 44"><rect x="4" y="18" width="36" height="24" rx="3" fill="#fff"/><rect x="16" y="4" width="12" height="12" rx="2" fill="none" stroke="#fff" stroke-width="2.5"/><g fill="var(--navy)"><circle cx="12" cy="26" r="3"/><circle cx="22" cy="26" r="3"/><circle cx="32" cy="26" r="3"/><circle cx="12" cy="35" r="3"/><circle cx="22" cy="35" r="3"/><circle cx="32" cy="35" r="3"/></g><rect x="19" y="8" width="6" height="5" fill="var(--lime)"/></svg>
          MEDICATION<br>ADDICTION
        </div>
        <div class="issue">
          <svg viewBox="0 0 44 44"><circle cx="22" cy="24" r="7" fill="#fff"/><path d="M8 44a14 12 0 0 1 28 0z" fill="#fff"/><circle cx="10" cy="8" r="4" fill="none" stroke="#fff" stroke-width="2"/><circle cx="22" cy="6" r="4" fill="none" stroke="#fff" stroke-width="2"/><circle cx="34" cy="10" r="4" fill="var(--lime)"/></svg>
          BEHAVIORAL<br>HEALTH
        </div>
      </div>
    </section>

    <h2 class="abs why">WHY CHOOSE US?</h2>

    <div class="stat stat-years"><div class="num">100+</div><div class="label">YEARS</div><p class="note">Over 100 years of medical and clinical experience behind our team</p></div>
    <div class="stat stat-rating"><div class="num">95%</div><div class="label">SATISFACTION<br>RATING</div><p class="note">Our patients rate us 95 out of 100</p></div>
    <div class="stat stat-best"><div class="num">#1</div><div class="label">BEST DRUG &amp;<br>ALCOHOL<br>REHAB CENTER</div><p class="note">Voted one of the best Alcohol and Drug rehab centers</p></div>
    <div class="stat stat-treated"><div class="num">2500+</div><div class="label">PATIENTS<br>TREATED</div><p class="note">Over 2,500 patients treated successfully and counting</p></div>

    <div class="abs rooms" role="img" aria-label="Photos of the residence: bunk bed bedrooms, a meeting room and comfortable living rooms">
      <div class="room-a"></div><div class="room-b"></div><div class="room-c"></div>
      <div class="room-d"></div><div class="room-e"></div><div class="room-f"></div>
    </div>
    <div class="abs spaces">
      <h3>SPACES AVAILABLE</h3>
      <p>with capacity of 16 men, split into two groups of 8.<br>This ensures treatment is individualised.</p>
    </div>

    <div class="abs brand-mark"></div>
    <div class="abs brand-name">Corvalmend</div>

    <div class="abs contact">
      <p class="kicker">Our caring team will help<br>answer any questions you have</p>
      <p class="lead">Get in touch with us now.<br>We're here to help!</p>
      <p class="row"><svg viewBox="0 0 16 16"><path d="M3 1l3 3-1.5 2a9 9 0 0 0 5.5 5.5L12 10l3 3-2 2C7 15 1 9 1 3z" fill="var(--green)"/></svg>859-555-0148</p>
      <p class="row"><svg viewBox="0 0 16 16"><rect x="1" y="3" width="14" height="10" fill="var(--green)"/><path d="M1 3l7 6 7-6" fill="none" stroke="#fff" stroke-width="1.5"/></svg>Admissions@corvalmend.org</p>
      <p class="web">www.corvalmend.org</p>
    </div>

    <div class="footer-bar"></div>
  </main>

  <main class="page page-back">
    <div class="abs back-header">
      <div class="abs team-photo" role="img" aria-label="Photo of two smiling program graduates holding their certificates outdoors"></div>
    </div>
    <h2 class="abs programs-title"><span class="accent">Treatment</span>Programs</h2>
    <div class="abs programs-copy">
      <p>We provide three personalized treatment options for individuals struggling with addiction.</p>
      <p>Our treatment philosophy is to treat clients with the lowest dose of Medication Assisted Therapy ('MAT') to remove their cravings and withdrawals so that they may begin their path of rehabilitation without the physical obstacles to recovery.</p>
      <p>We believe clients can successfully taper off 'MAT' after acquiring the support and skills they need to obtain their goal of sobriety.</p>
    </div>

    <h2 class="abs works-title">WHY TREATMENT HERE WORKS</h2>

    <div class="feature f-evidence">
      <div class="icon"><span></span></div>
      <div><h4>Evidence Based Treatment</h4><p>We use evidence-based treatment that has been scientifically tested and proven to produce positive results. Ranging from cognitive behaviour therapy to dialectical therapy, we do what it takes to make you healthy.</p></div>
    </div>
    <div class="feature f-tele">
      <div class="icon"><span></span></div>
      <div><h4>Telemedicine</h4><p>Corvalmend is offering aspects of its treatment program via telehealth services to meet the need of clients seeking treatment from the convenience of their homes.</p></div>
    </div>
    <div class="feature f-individual">
      <div class="icon"><span></span></div>
      <div><h4>Individualized</h4><p>You deserve individualized attention from experienced professionals who actually care. Our reputation, small case load and success rates mean you are given the best treatment from leading experts.</p></div>
    </div>
    <div class="feature f-mat">
      <div class="icon"><span></span></div>
      <div><h4>Medication Assisted Treatment</h4><p>Medication assisted treatment helps to relieve withdrawal symptoms and cravings which makes going clean easier.We treat addiction with FDA-approved medicines to help you focus on your recovery. We prescribe medicines such as buprenorphine.</p></div>
    </div>

    <blockquote class="quote q-left">
      <span class="mark open">&ldquo;</span>
      <p>Great people, they changed my life in so many ways. Dylan stopped his daily life to come to court with me to help me out of a bad spot. They're not just a doc office, they're people who want to make a difference. I love u all thanks for the help you have given me.</p>
      <p class="author">-JORDAN M</p>
      <span class="mark close">&rdquo;</span>
    </blockquote>
    <blockquote class="quote q-right">
      <span class="mark open">&ldquo;</span>
      <p>Corvalmend and their team have made a difference in my life. They genuinely care about their clients. They have went above and beyond to help me. Everyone is very polite and caring</p>
      <p class="author">-KELLY R</p>
      <span class="mark close">&rdquo;</span>
    </blockquote>

    <h3 class="abs insure-title">MOST INSURANCES ACCEPTED</h3>
    <div class="abs insurers">
      <span>Carewell</span><span>Pinebrook</span><span>Lumenra</span><span>Harborly</span><span>Unity Shield</span><span>Blueleaf</span><span>Passway</span><span>Meridia</span>
    </div>

    <div class="abs transport">
      <div class="transport-tag">FREE TRANSPORT<br>ASSISTANCE AVAILABLE</div>
      <div class="location loc-a">
        <svg viewBox="0 0 10 14"><path d="M5 0a5 5 0 0 1 5 5c0 4-5 9-5 9S0 9 0 5a5 5 0 0 1 5-5z" fill="var(--green)"/><circle cx="5" cy="5" r="2" fill="#fff"/></svg>
        <div><b>Corvalmend Burlington,<br>Kentucky</b><br>4120 Sample Pkwy, Burlington, KY 41005</div>
      </div>
      <div class="location loc-b">
        <svg viewBox="0 0 10 14"><path d="M5 0a5 5 0 0 1 5 5c0 4-5 9-5 9S0 9 0 5a5 5 0 0 1 5-5z" fill="var(--green)"/><circle cx="5" cy="5" r="2" fill="#fff"/></svg>
        <div><b>Corvalmend Richmond,<br>Kentucky</b><br>870 Example Ln, Richmond, KY 40475</div>
      </div>
    </div>

    <p class="abs back-lead">Get in touch with us now.<br>We're here to help!</p>
    <div class="abs back-rows">
      <p class="row"><svg viewBox="0 0 16 16"><path d="M3 1l3 3-1.5 2a9 9 0 0 0 5.5 5.5L12 10l3 3-2 2C7 15 1 9 1 3z" fill="var(--green)"/></svg>859-555-0148</p>
      <p class="row"><svg viewBox="0 0 16 16"><rect x="1" y="3" width="14" height="10" fill="var(--green)"/><path d="M1 3l7 6 7-6" fill="none" stroke="#fff" stroke-width="1.5"/></svg>Admissions@corvalmend.org</p>
    </div>
    <div class="abs web-pill">www.corvalmend.org</div>

    <div class="footer-bar"></div>
  </main>

</div>
</body>
</html>
```